Business Card Design

We need a business card designed for our new company. Prefer a black card with white logo & writing.

Contact Information for Business Card

Ted Galloway, address: 7-4812 Fernhollow Road, Abbotsford, BC, V3K 8R2, Office Phone: 604-712-3390, Cell: 604-947-2164, Email: ted@resinworkshub.ca

Colors

Designer to choose only greyscale colors for use in the design.

```html
<!DOCTYPE html>
<html lang="en">
<head>
<meta charset="utf-8">
<title>Resinworks Hub — Business Card</title>
<link rel="stylesheet" href="https://fonts.googleapis.com/css2?family=Poppins:wght@300;400;700&display=swap">
<style>
  :root {
    --stage: #232323;
    --card: #2b2b2d;
    --pattern-top: #3a3a3c;
    --pattern-bottom: #1f1f21;
    --ink: #ffffff;
    --ink-soft: #e6e6e6;
  }
  * { box-sizing: border-box; margin: 0; padding: 0; }
  html, body {
    width: 1200px; height: 711px; overflow: hidden;
    background: var(--stage);
    font-family: "Poppins", sans-serif;
    color: var(--ink);
  }
  .stage {
    position: relative; width: 1200px; height: 711px;
    display: flex; align-items: center; justify-content: center; gap: 44px;
  }
  .card {
    position: relative; width: 536px; height: 306px;
    background: var(--card);
    border-radius: 3px;
    overflow: hidden;
    box-shadow: 0 10px 30px rgba(0,0,0,.55);
  }
  /* Back side */
  .card-back .pattern-area {
    position: absolute; inset: 0;
    background: linear-gradient(160deg, var(--pattern-top), var(--pattern-bottom));
  }
  .card-back .brand-small {
    position: absolute; right: 30px; bottom: 30px;
    display: flex; align-items: center; gap: 8px;
    font-weight: 700; font-size: 15px; letter-spacing: .5px;
  }
  .brand-dot {
    width: 10px; height: 10px; border-radius: 50%; background: var(--ink);
  }
  /* Front side */
  .card-front .name-bar {
    position: absolute; left: 22px; top: 58px; width: 5px; height: 40px;
    background: var(--ink);
  }
  .card-front .identity { position: absolute; left: 36px; top: 54px; }
  .name { font-size: 26px; line-height: 1.05; font-weight: 300; }
  .name strong { font-weight: 700; }
  .role { font-size: 11px; font-weight: 300; color: var(--ink-soft); }
  .brand-large {
    position: absolute; right: 40px; top: 70px;
    display: flex; align-items: center; gap: 12px;
    font-weight: 700; font-size: 30px; letter-spacing: 1px; text-transform: uppercase;
  }
  .brand-large .brand-dot { width: 18px; height: 18px; }
  .address {
    position: absolute; left: 66px; top: 176px;
    font-size: 11px; font-weight: 300; line-height: 1.35; color: var(--ink-soft);
  }
  .contacts {
    position: absolute; left: 66px; top: 216px; list-style: none;
    font-size: 11px; font-weight: 300; line-height: 1.45; color: var(--ink-soft);
  }
  .contacts li { display: flex; align-items: center; gap: 8px; }
  .contacts svg { width: 10px; height: 10px; fill: var(--ink); flex: none; }
</style>
</head>
<body>
<main class="stage">
  <section class="card card-back">
    <div class="pattern-area" role="img" aria-label="Embossed repeating mountain-ridge pattern in dark greys"></div>
    <div class="brand-small"><span class="brand-dot"></span>Resinworks Hub</div>
  </section>

  <section class="card card-front">
    <div class="name-bar"></div>
    <div class="identity">
      <h1 class="name"><strong>Ted</strong> Galloway</h1>
      <p class="role">Founder &amp; CEO</p>
    </div>
    <div class="brand-large"><span class="brand-dot"></span>Resinworks Hub</div>
    <address class="address">7-4812 Fernhollow Road,<br>Abbotsford, BC, V3K 8R2.</address>
    <ul class="contacts">
      <li><svg viewBox="0 0 10 10"><path d="M2 0.5l2 2-1 1.2c.6 1.3 1.6 2.3 2.9 2.9L7 5.5l2 2-1.3 1.8C4 9 1 6 .7 2.3z"/></svg>604-712-3390</li>
      <li><svg viewBox="0 0 10 10"><path d="M2.5 0h5v10h-5zM3.3 1v7h3.4V1z"/></svg>604-947-2164</li>
      <li><svg viewBox="0 0 10 10"><path d="M5 0a5 5 0 100 10A5 5 0 005 0zm0 1.2a3.8 3.8 0 013.7 3H1.3a3.8 3.8 0 013.7-3zm-3.7 4.6h7.4a3.8 3.8 0 01-7.4 0z"/></svg>www.resinworkshub.ca</li>
      <li><svg viewBox="0 0 10 10"><path d="M0 2h10v6.5H0zm1 .8L5 5.6 9 2.8z"/></svg>ted@resinworkshub.ca</li>
    </ul>
  </section>
</main>
</body>
</html>
```